Media Services Start-up -- Corporate Website and Logo Design. Inspiration required!

We need a logo design and corporate website design, including coding, for our start-up business.
Vennatra’s value proposition is based on bringing together media content from a vast number of geographies globally, adding human and AI curation, translation and editing, and delivering the content using tailored customer interfaces. On the one hand, the business brings together media coverage from all over the world, and on the other it brings together content, human skills and technology to deliver a supreme customer experience.
Vennatra is a B2B media monitoring and analytics business with emphasis on global customers. Vennatra's service offering is centred around sourcing media content from different markets, processing, storing and delivering the content and insights derived from it using an online platform / mobile app.
The messaging we want to create through the logo is:
- Global scope
- Speed of delivery
- Cost-efficiency
- Multi-lingual
- Tailor-made
- Trustworthy
Target Market(s)
Business to business, PR / Communications, Media, Marketing
Logo Text
Vennatra
Coding
Coded - Design and coding required
Number of Pages Required
5+ page
Font styles to use
Other font styles liked:
- See Design Brief for details
Colors
Designer to choose colors to be used in the design.

```html
<!DOCTYPE html>
<html lang="en">
<head>
<meta charset="utf-8">
<title>Vennatra — Global Media Intelligence</title>
<link href="https://fonts.googleapis.com/css2?family=Roboto:wght@400;500;700&display=swap" rel="stylesheet">
<style>
:root{
  --teal:#3aae9c;
  --grey-text:#5e5e5e;
  --logo-grey:#5a5a5a;
  --white:#ffffff;
  --dark:#0d0d0d;
  --field:#5a5a5a;
  --frame:#cfcfcf;
}
*{margin:0;padding:0;box-sizing:border-box}
html,body{width:1200px;height:544px;overflow:hidden}
body{font-family:'Roboto',sans-serif;background:var(--white);position:relative}

.site-header{position:absolute;left:0;top:0;width:1200px;height:85px;background:var(--white)}
.brand{position:absolute;left:140px;top:12px;font-size:50px;font-weight:700;color:var(--logo-grey);letter-spacing:-.5px}
.contact-bar{position:absolute;right:142px;top:10px;display:flex;gap:26px;align-items:center;font-size:14px;color:var(--grey-text)}
.contact-item{display:flex;align-items:center;gap:9px}
.contact-icon{width:27px;height:27px;border:1.5px solid var(--teal);border-radius:50%;display:flex;align-items:center;justify-content:center}
.main-nav{position:absolute;right:141px;top:49px;display:flex;align-items:center}
.main-nav a{font-size:14.5px;color:var(--grey-text);text-decoration:none;margin-left:26px}
.main-nav .sign-in{background:var(--teal);color:var(--white);padding:0 15px;height:29px;line-height:29px;font-size:15.5px;margin-left:18px}

.hero{position:absolute;left:0;top:85px;width:1200px;height:423px;overflow:hidden}
.hero-visual{position:absolute;inset:0;background:radial-gradient(ellipse at 48% 55%,#4a4a4a 0%,#262626 35%,#0f0f0f 75%)}
.hero-copy{position:absolute;left:140px;top:84px;color:var(--white)}
.hero-title{font-size:31px;font-weight:700;line-height:38px;letter-spacing:.2px}
.hero-text{margin-top:12px;width:340px;font-size:15.5px;line-height:25px;letter-spacing:.2px}
.hero-cta{display:inline-block;margin-top:19px;background:var(--white);color:#111;font-size:15px;padding:0 13px;height:40px;line-height:40px;box-shadow:6px 5px 0 -4px rgba(255,255,255,.35)}

.lead-form{position:absolute;left:752px;top:42px;width:305px;height:339px;background:var(--dark);border:7px solid var(--frame);padding:0 14px}
.lead-form h2{margin-top:26px;font-size:20px;font-weight:700;color:var(--white)}
.field{margin-top:15px;height:42px;background:var(--field);display:flex;align-items:center;padding-left:9px;gap:7px;color:var(--white);font-size:12.5px}
.lead-form h2 + .field{margin-top:21px}
.submit{margin-top:15px;height:42px;background:var(--teal);color:var(--white);font-size:17px;font-weight:500;display:flex;align-items:center;justify-content:center}

.site-footer{position:absolute;left:0;top:508px;width:1200px;height:36px;background:var(--teal);color:var(--white)}
.copyright{position:absolute;left:143px;top:10px;font-size:13px}
.social{position:absolute;right:142px;top:11px;display:flex;gap:10px}
.social span{width:14px;height:14px;border-radius:50%;background:var(--white)}
</style>
</head>
<body>
<header class="site-header">
  <div class="brand">Vennatra</div>
  <div class="contact-bar">
    <div class="contact-item">
      <span class="contact-icon"><svg width="13" height="13" viewBox="0 0 24 24"><path fill="#5e5e5e" d="M6.6 10.8a15 15 0 0 0 6.6 6.6l2.2-2.2a1 1 0 0 1 1-.25 11.4 11.4 0 0 0 3.6.57 1 1 0 0 1 1 1V20a1 1 0 0 1-1 1A17 17 0 0 1 3 4a1 1 0 0 1 1-1h3.5a1 1 0 0 1 1 1c0 1.25.2 2.45.57 3.6a1 1 0 0 1-.25 1z"/></svg></span>
      +1 555 010 2040
    </div>
    <div class="contact-item">
      <span class="contact-icon"><svg width="13" height="10" viewBox="0 0 24 18"><rect x="1" y="1" width="22" height="16" fill="#5e5e5e"/><path d="M1 1l11 9 11-9" stroke="#fff" stroke-width="2" fill="none"/></svg></span>
      info@vennatra.com
    </div>
  </div>
  <nav class="main-nav">
    <a href="#">Home</a><a href="#">Solutions</a><a href="#">How We Do It</a><a href="#">Our People</a><a href="#">Our Technology</a>
    <a href="#" class="sign-in">SIGN IN</a>
  </nav>
</header>

<section class="hero">
  <div class="hero-visual" role="img" aria-label="Dark monochrome scene of a businessman facing a glowing globe over a city skyline, with network lines and technology icons"></div>
  <div class="hero-copy">
    <h1 class="hero-title">DELIVERING GLOBAL<br>MEDIA INTELLIGENCE</h1>
    <p class="hero-text">Vennatra is an international media intelligence service provider. We help communications teams build and operate truly global media monitoring and measurement programmes.</p>
    <a class="hero-cta" href="#">CONTACT US TODAY</a>
  </div>
  <form class="lead-form">
    <h2>Learn More About Vennatra</h2>
    <div class="field"><svg width="14" height="14" viewBox="0 0 24 24"><circle cx="12" cy="7" r="5" fill="#fff"/><path d="M2 23c0-6 4.5-9 10-9s10 3 10 9z" fill="#fff"/></svg>Your Name*</div>
    <div class="field"><svg width="14" height="11" viewBox="0 0 24 18"><rect x="1" y="1" width="22" height="16" fill="#fff"/><path d="M1 1l11 9 11-9" stroke="#5a5a5a" stroke-width="2" fill="none"/></svg>Your Email*</div>
    <div class="field"><svg width="14" height="14" viewBox="0 0 24 24"><path fill="#fff" d="M6.6 10.8a15 15 0 0 0 6.6 6.6l2.2-2.2a1 1 0 0 1 1-.25 11.4 11.4 0 0 0 3.6.57 1 1 0 0 1 1 1V20a1 1 0 0 1-1 1A17 17 0 0 1 3 4a1 1 0 0 1 1-1h3.5a1 1 0 0 1 1 1c0 1.25.2 2.45.57 3.6a1 1 0 0 1-.25 1z"/></svg>Your Phone*</div>
    <div class="submit">GET STARTED</div>
  </form>
</section>

<footer class="site-footer">
  <div class="copyright">Copyright © 2019 Vennatra. All Rights Reserved.</div>
  <div class="social"><span></span><span></span><span></span></div>
</footer>
</body>
</html>
```